Dynamic Business Card for Sports Supplements Company

Hi! I'm looking for an awesome business card to match my existing sports supplement company. I have uploaded my current company logo and screenshot of the front page of my website.

I would like to have something dynamic and interesting and utilize the colors in the website - the reds and purples

The business card should be double sided and focus on a unique eye-catching design on the back and include all the relevant company info.

Most importantly, it should say somewhere: "Sign up on our website for a coupon code."

Target Market(s)

Mostly for women gym goers but it shouldn't be too feminine. It should be in keeping with the website design. It should flow and clearly be connected to it

Industry/Entity Type

Business

Contact Information for Business Card

Lorraine K. Vestal
CEO
LVestal@Quorvanexco.com
www.quorvanexco.com
555.417.3820
P.O. Box 47315
Carrow Ridge, Vermont 00000

Sign up on our website for a coupon code

Font styles to use
Serif
Sans Serif
Other font styles liked:
• Novecento font family and "Quorvanex" is in AR Destine font

Requirements
Must have
• One side should be a bold Quorvanex logo design. Even just the symbol itself may be o.k. (see attached file)

```html
<!DOCTYPE html>
<html lang="en">
<head>
<meta charset="utf-8">
<title>Quorvanex Business Card</title>
<link href="https://fonts.googleapis.com/css2?family=Open+Sans:wght@400;600;700;800&display=swap" rel="stylesheet">
<style>
  :root {
    --backdrop: #2b2b2d;
    --card: #0d0e14;
    --red: #e0252f;
    --white: #ffffff;
  }
  * { margin: 0; padding: 0; box-sizing: border-box; }
  html, body {
    width: 1200px; height: 880px; overflow: hidden;
    background: var(--backdrop);
    font-family: "Open Sans", Arial, sans-serif;
  }
  .canvas { position: relative; width: 1200px; height: 880px; }
  .card {
    position: absolute;
    width: 620px; height: 354px;
    background: var(--card);
    border-radius: 18px;
    color: var(--white);
    display: flex; flex-direction: column; align-items: center; justify-content: center;
    text-align: center;
    box-shadow: 0 14px 30px rgba(0,0,0,.45);
  }
  .card--front { left: 60px; top: 70px; }
  .card--back { left: 520px; top: 456px; }

  .brand { display: flex; flex-direction: column; align-items: center; }
  .brand__name {
    font-weight: 800; color: var(--white);
    letter-spacing: 2px; line-height: 1;
  }
  .brand__tagline {
    font-weight: 400; color: var(--white);
    letter-spacing: 3.4px; text-transform: uppercase;
    margin-top: 6px;
  }
  .card--front .brand__name { font-size: 48px; }
  .card--front .brand__tagline { font-size: 11px; }
  .website { margin-top: 34px; font-size: 16px; font-weight: 600; }
  .accent { color: var(--red); }

  .card--back .brand__name { font-size: 44px; }
  .card--back .brand__tagline { font-size: 10px; }
  .person { margin-top: 12px; }
  .person__name { color: var(--red); font-size: 21px; font-weight: 700; line-height: 1.15; }
  .person__role { font-size: 14px; }
  .contact { margin-top: 8px; font-size: 14.5px; line-height: 1.4; }
  .contact__label { color: var(--red); font-weight: 700; }
  .social { display: flex; gap: 8px; margin-top: 8px; }
  .social__dot { width: 24px; height: 24px; border: 2px solid var(--white); border-radius: 50%; }
  .signup { margin-top: 10px; font-size: 15px; }
</style>
</head>
<body>
<main class="canvas">
  <section class="card card--front" aria-label="Card front">
    <div class="brand">
      <span class="brand__name">QUORVANEX</span>
      <span class="brand__tagline">Your Strength Companion</span>
    </div>
    <p class="website">www.<span class="accent">quorvanexco</span>.com</p>
  </section>

  <section class="card card--back" aria-label="Card back">
    <div class="brand">
      <span class="brand__name">QUORVANEX</span>
      <span class="brand__tagline">Your Strength Companion</span>
    </div>
    <div class="person">
      <p class="person__name">Lorraine K. Vestal</p>
      <p class="person__role">CEO</p>
    </div>
    <div class="contact">
      <p><span class="contact__label">P:</span> 555.417.3820</p>
      <p><span class="contact__label">E:</span> LVestal@Quorvanexco.com</p>
      <p><span class="contact__label">A:</span> P.O. Box 47315 Carrow Ridge, Vermont 00000</p>
    </div>
    <div class="social" aria-label="Social links">
      <span class="social__dot"></span>
      <span class="social__dot"></span>
      <span class="social__dot"></span>
      <span class="social__dot"></span>
    </div>
    <p class="signup"><span class="accent">Sign up</span> on our website for a coupon code</p>
  </section>
</main>
</body>
</html>
```